Trading company needs a non alcoholic beer Can design

We KLW are trading company , food Distributors in Africa -RD Congo/Kinshasa .We want to do a Private label non alcoholic beer 500ml can and need a design for this Project .
the Brand Name is : RIVO BREW
We want it to be similar NOT a copy of Velmont 0.0% can ( picture
attached ) as we want to respect the intellectual properties .so we prefer to use the same colors but more elegant ,modern style .
thanks.
THE DESIGN MUST STATE ITS A NON ALCOHOLIC BEER
PLZ SEARCH FOR VELMONT 0.0% MALT DRINK YOU WILL FIND 2 DESIGNS OLD AND NEW WE NEED SOMTHING SIMILAR TO THESE DESIGNS ,KINDLY USE SAME COLORS AND THE 0.0% SHOULD BE IN THE MIDDLE OF THE CAN .
Target Market(s)
THE PRODUCT WILL BE SOLD IN THE SUPERMASRKTS / MODERN TRADE
Look and feel

```html
<!DOCTYPE html>
<html lang="en">
<head>
<meta charset="utf-8">
<title>RIVO BREW 0.0% Can Label</title>
<link rel="stylesheet" href="https://fonts.googleapis.com/css2?family=Playfair+Display:wght@600&family=Great+Vibes&family=Montserrat:ital,wght@0,600;0,700;0,800;1,700&display=swap">
<style>
  :root {
    --backdrop: #e7e7e9;
    --red: #d7341c;
    --red-deep: #b81f0c;
    --blue: #2d58a8;
    --blue-deep: #1e3f86;
    --gold: #d9b24a;
    --white: #ffffff;
    --silver-light: #e2e2e4;
    --silver-dark: #b9b9bd;
  }
  * { margin: 0; padding: 0; box-sizing: border-box; }
  html, body {
    width: 960px;
    height: 1200px;
    overflow: hidden;
    background: var(--backdrop);
  }
  .canvas {
    position: relative;
    width: 960px;
    height: 1200px;
  }
  .can-label {
    position: absolute;
    left: 160px;
    top: 40px;
    width: 640px;
    height: 1120px;
    display: block;
  }
  .brand-name { font-family: "Playfair Display", serif; font-weight: 600; }
  .brand-tag { font-family: "Great Vibes", cursive; }
  .sans { font-family: "Montserrat", sans-serif; }
</style>
</head>
<body>
<main class="canvas">
  <svg class="can-label" viewBox="0 0 640 1120" xmlns="http://www.w3.org/2000/svg" aria-label="RIVO BREW non alcoholic beer can label">
    <defs>
      <linearGradient id="silverSide" x1="0" x2="1" y1="0" y2="0">
        <stop offset="0" stop-color="var(--silver-dark)"/>
        <stop offset="1" stop-color="var(--silver-light)"/>
      </linearGradient>
      <linearGradient id="silverSideRight" x1="1" x2="0" y1="0" y2="0">
        <stop offset="0" stop-color="var(--silver-dark)"/>
        <stop offset="1" stop-color="var(--silver-light)"/>
      </linearGradient>
      <linearGradient id="redColumn" x1="0" x2="0" y1="0" y2="1">
        <stop offset="0" stop-color="var(--red-deep)"/>
        <stop offset="0.15" stop-color="var(--red)"/>
        <stop offset="1" stop-color="var(--red)"/>
      </linearGradient>
      <linearGradient id="blueLabel" x1="0" x2="0" y1="0" y2="1">
        <stop offset="0" stop-color="var(--blue)"/>
        <stop offset="1" stop-color="var(--blue-deep)"/>
      </linearGradient>
      <linearGradient id="figureBlue" x1="0" x2="0" y1="0" y2="1">
        <stop offset="0" stop-color="#5b86c4"/>
        <stop offset="0.5" stop-color="#e8eef7"/>
        <stop offset="0.52" stop-color="#3f6fb8"/>
        <stop offset="1" stop-color="#2a5aa6"/>
      </linearGradient>
    </defs>

    <!-- side panels -->
    <rect class="side-panel" x="0" y="0" width="66" height="1120" fill="url(#silverSide)" role="img" aria-label="silver halftone dot pattern"/>
    <rect class="side-panel" x="574" y="0" width="66" height="1120" fill="url(#silverSideRight)" role="img" aria-label="silver halftone dot pattern"/>

    <!-- central red column -->
    <rect class="red-column" x="66" y="0" width="508" height="1120" fill="url(#redColumn)" role="img" aria-label="red column with soft dot pattern"/>

    <!-- brand badge -->
    <g class="brand-badge">
      <circle cx="320" cy="250" r="50" fill="var(--blue)" stroke="var(--white)" stroke-width="4"/>
      <text class="sans" x="320" y="256" text-anchor="middle" font-size="13" font-weight="700" fill="var(--white)">RIVO BREW</text>
    </g>

    <!-- blue brand label -->
    <g class="brand-label">
      <path d="M0,380 L34,344 Q320,268 606,344 L640,380 L640,500 L606,536 Q320,612 34,536 L0,500 Z" fill="var(--white)"/>
      <path d="M8,382 L40,352 Q320,280 600,352 L632,382 L632,498 L600,528 Q320,600 40,528 L8,498 Z" fill="url(#blueLabel)"/>
      <path d="M20,386 L48,362 Q320,294 592,362 L620,386 L620,494 L592,518 Q320,586 48,518 L20,494 Z" fill="none" stroke="var(--gold)" stroke-width="3"/>
      <rect x="248" y="372" width="144" height="14" rx="7" fill="var(--gold)" opacity="0.8" role="img" aria-label="gold flourish ornament"/>
      <ellipse cx="66" cy="450" rx="16" ry="44" fill="var(--gold)" opacity="0.85" role="img" aria-label="gold wheat laurel"/>
      <ellipse cx="574" cy="450" rx="16" ry="44" fill="var(--gold)" opacity="0.85" role="img" aria-label="gold wheat laurel"/>
      <text class="brand-name" x="320" y="470" text-anchor="middle" font-size="76" fill="var(--white)">RIVO BREW</text>
      <text class="brand-tag" x="320" y="522" text-anchor="middle" font-size="44" fill="var(--white)">Premium</text>
    </g>

    <!-- alcohol free band -->
    <g class="abv-band">
      <polygon points="74,640 560,600 566,846 70,886" fill="var(--white)"/>
      <text class="sans" x="300" y="808" text-anchor="middle" font-size="190" font-weight="800" fill="url(#figureBlue)" letter-spacing="-8">0.0</text>
      <text class="sans" x="475" y="720" text-anchor="middle" font-size="96" font-weight="800" fill="var(--blue)">%</text>
      <text class="sans" x="478" y="770" text-anchor="middle" font-size="34" font-weight="800" fill="var(--blue)">ALC.</text>
    </g>

    <!-- product descriptor -->
    <g class="descriptor">
      <text class="sans" x="320" y="960" text-anchor="middle" font-size="28" font-weight="700" fill="var(--white)" letter-spacing="2">PREMIUM</text>
      <text class="sans" x="320" y="1012" text-anchor="middle" font-size="56" font-weight="600" fill="var(--white)" letter-spacing="1">ORIGINAL</text>
      <text class="sans" x="320" y="1042" text-anchor="middle" font-size="18" font-weight="600" fill="var(--white)" letter-spacing="1">NON ALCOHOLIC BEER</text>
      <line x1="260" y1="1062" x2="380" y2="1062" stroke="var(--white)" stroke-width="2"/>
    </g>

    <text class="sans volume" x="320" y="1104" text-anchor="middle" font-size="26" font-style="italic" font-weight="700" fill="var(--white)">500ml</text>
  </svg>
</main>
</body>
</html>
```